female esthetician looking for an impact business card

I an an expert in skin care industry with high experience in NYC.I want my business card to look professional , an impact at first look. I do want a combination between white and gold . I believe the font will be great if is gold.. The Fonts are also important. MIRABELA COSTINA (SKIN CARE BOUTIQUE)

THIS SHOULD BE THE BUSINESS NAME, and should be placed on th eback of the card.
IN front m, the name MIRABELA COSTINA - ESTHETCIAN

BY APPOINTMENTS ONLY: 518.240.7136

Target Market(s)

HIGH END CLIENTELE

Contact Information for Business Card

iT WILL BE on a luxury paper. I neeed the wow feeling

Requirements
Should not have
• pictures

```html
<!DOCTYPE html>
<html lang="en">
<head>
<meta charset="utf-8">
<title>Mirabela Costina — Business Card</title>
<link rel="stylesheet" href="https://fonts.googleapis.com/css2?family=Cinzel:wght@500;600&family=Quicksand:wght@400;500&display=swap">
<style>
  :root {
    --backdrop: #e9ecea;
    --card: #ffffff;
    --gold: #b5762a;
    --gold-light: #d9a84e;
    --gold-deep: #8f5318;
    --ink-soft: #7b7f80;
    --mint: #74bf9b;
    --leaf-deep: #3f8c63;
    --leaf-pale: #cfe6d8;
  }
  * { margin: 0; padding: 0; box-sizing: border-box; }
  html, body {
    width: 1200px;
    height: 1000px;
    overflow: hidden;
    background: var(--backdrop);
  }
  .stage {
    position: relative;
    width: 1200px;
    height: 1000px;
  }
  .business-card {
    position: absolute;
    left: 390px;
    top: 155px;
    width: 420px;
    height: 690px;
    background: var(--card);
    box-shadow: 0 10px 30px rgba(60, 70, 65, 0.12);
    overflow: hidden;
  }
  .gold-frame {
    position: absolute;
    left: 22px;
    top: 22px;
    right: 22px;
    bottom: 40px;
    border: 3px solid var(--gold);
    border-image: linear-gradient(160deg, var(--gold-deep), var(--gold-light) 45%, var(--gold) 70%, var(--gold-light)) 1;
  }
  .foliage {
    position: absolute;
    border-radius: 40% 10% 45% 20%;
  }
  .foliage--top-right {
    right: -10px;
    top: -10px;
    width: 230px;
    height: 180px;
    background: radial-gradient(ellipse at 70% 35%, var(--leaf-deep) 0%, var(--mint) 35%, var(--leaf-pale) 65%, rgba(255,255,255,0) 80%);
    opacity: 0.8;
  }
  .foliage--bottom-left {
    left: -10px;
    bottom: 10px;
    width: 280px;
    height: 170px;
    background: radial-gradient(ellipse at 45% 60%, var(--leaf-deep) 0%, var(--mint) 35%, var(--leaf-pale) 62%, rgba(255,255,255,0) 80%);
    opacity: 0.8;
  }
  .identity {
    position: absolute;
    left: 0;
    right: 0;
    top: 240px;
    text-align: center;
    color: var(--gold);
  }
  .identity__name {
    font-family: "Cinzel", serif;
    font-weight: 600;
    font-size: 30px;
    letter-spacing: 0.5px;
    line-height: 1;
  }
  .identity__title {
    font-family: "Quicksand", sans-serif;
    font-weight: 500;
    font-size: 21px;
    letter-spacing: 1.5px;
    margin-top: 4px;
  }
  .contact-list {
    position: absolute;
    left: 90px;
    top: 378px;
    list-style: none;
    font-family: "Quicksand", sans-serif;
    font-weight: 500;
    font-size: 17px;
    color: var(--ink-soft);
    line-height: 21px;
  }
  .contact-list__item {
    display: flex;
    align-items: flex-start;
    margin-bottom: 5px;
  }
  .contact-list__icon {
    flex: 0 0 16px;
    width: 16px;
    height: 16px;
    margin: 3px 10px 0 0;
  }
</style>
</head>
<body>
<main class="stage">
  <article class="business-card">
    <div class="foliage foliage--top-right" role="img" aria-label="Watercolour green leaf sprigs in the top right corner"></div>
    <div class="foliage foliage--bottom-left" role="img" aria-label="Watercolour green leaf sprigs in the bottom left corner"></div>
    <div class="gold-frame"></div>

    <header class="identity">
      <h1 class="identity__name">MIRABELA COSTINA</h1>
      <p class="identity__title">skin care expert</p>
    </header>

    <ul class="contact-list">
      <li class="contact-list__item">
        <svg class="contact-list__icon" viewBox="0 0 24 24" aria-hidden="true">
          <path fill="var(--mint)" d="M6.6 10.8a15.1 15.1 0 0 0 6.6 6.6l2.2-2.2a1 1 0 0 1 1-.25 11.4 11.4 0 0 0 3.6.57 1 1 0 0 1 1 1V20a1 1 0 0 1-1 1A17 17 0 0 1 3 4a1 1 0 0 1 1-1h3.5a1 1 0 0 1 1 1c0 1.25.2 2.46.57 3.58a1 1 0 0 1-.25 1z"/>
        </svg>
        <span>+1.518.240.7136</span>
      </li>
      <li class="contact-list__item">
        <svg class="contact-list__icon" viewBox="0 0 24 24" aria-hidden="true">
          <rect x="2.5" y="5" width="19" height="14" fill="none" stroke="var(--mint)" stroke-width="2"/>
          <path d="M2.5 5l9.5 8 9.5-8M2.5 19l7-6.5M21.5 19l-7-6.5" fill="none" stroke="var(--mint)" stroke-width="2"/>
        </svg>
        <span>hello@mirabelacostina.com</span>
      </li>
      <li class="contact-list__item">
        <svg class="contact-list__icon" viewBox="0 0 24 24" aria-hidden="true">
          <path fill="var(--mint)" d="M12 2a7 7 0 0 0-7 7c0 5.2 7 13 7 13s7-7.8 7-13a7 7 0 0 0-7-7zm0 9.6A2.6 2.6 0 1 1 12 6.4a2.6 2.6 0 0 1 0 5.2z"/>
        </svg>
        <span>Level 3, 18 Linden Lane<br>Brookvale Heights, Australia</span>
      </li>
    </ul>
  </article>
</main>
</body>
</html>
```